Semi-anonymous photo sharing and messaging app

Design app interface. App is needed for semi-anonymous communication.

For instance if you are on a tour bus, and you just met some people there. You want to send them pictures, but you don't want to give your chatterbox / email / phone number. So instead you use this app - current name is "eLumix" but you can also suggest a name if it fits really well with the theme of the design.

The initial version of the app is in the vantor store
https://apps.vantorhub.example/store/apps/details?id=com.qz7mwplk3rt9bvne5hsyc

the web version of this app is located here
https://tallbluekites.example/

it is called Tall Blue Kites, because the password is four common words, and if you know those words, you can open the chat room.

As you can see app looks very poorly, and needs to be designed from bottom up. App should look nothing like it looks now. it should have original and easily recognizable feel to it.

I'm attaching screen-shots of the current app. Two screens - you enter password on one screen (or choose one of the existing "rooms") - you chat with peers on the second screen

It should be something neutral, so it's mainly for travellers, but could be used by anyone else. It should have vibe of comfort and security, but at the same time adventure and fun.

Please come back with more questions!

Target Market(s)

Travellers, mostly
single, groups,

Industry/Entity Type

Communication

Font styles to use
Sans Serif

Requirements
Must have
• original, light feel
• recognizable
• unique

```html
<!DOCTYPE html>
<html lang="en">
<head>
<meta charset="utf-8">
<title>Tall Blue Kites – Side Menu</title>
<link href="https://fonts.googleapis.com/css2?family=Roboto:wght@300;400;500;700&display=swap" rel="stylesheet">
<style>
  :root{
    --panel-top:#22365f;
    --panel-mid:#4a5878;
    --panel-warm:#5b4b47;
    --panel-low:#3a3533;
    --panel-bottom:#1d1c1c;
    --status-bg:#223560;
    --text-light:#ffffff;
    --text-soft:#c9ccd6;
    --text-muted:#9a9a9a;
    --divider:rgba(255,255,255,0.35);
    --badge:#5fa8f2;
    --band:#262525;
    --pill:#1c1c1c;
    --count:#3c3b3b;
    --strip-bar:#d9d2c6;
    --bubble:#ffffff;
    --bubble-text:#6c6c6c;
    --action-bar:#1d8fe3;
    --action-btn:#f2f2f2;
    --avatar-fill:#5f6e52;
  }
  *{box-sizing:border-box;margin:0;padding:0}
  html,body{width:676px;height:1200px;overflow:hidden;background:#fff}
  body{font-family:"Roboto",sans-serif}
  .screen{position:absolute;left:0;top:0;width:640px;height:1136px;transform:scale(1.05625);transform-origin:0 0;overflow:hidden}

  .conversation-strip{position:absolute;left:535px;top:0;width:105px;height:1136px;background:linear-gradient(180deg,#f1ede8 0%,#cfc5b5 30%,#e8e2da 45%,#b9ad9a 60%,#efebe6 75%,#f3f3f3 100%)}
  .strip-status{position:absolute;left:0;top:0;width:105px;height:46px;background:var(--status-bg)}
  .strip-header{position:absolute;left:0;top:46px;width:105px;height:66px;background:var(--strip-bar)}
  .mail-icon{position:absolute;left:33px;top:60px}
  .strip-avatar{position:absolute;left:12px;width:92px;height:92px;border-radius:50%;background:radial-gradient(circle at 50% 45%,#6d5a4a 0%,#3d4a55 55%,var(--avatar-fill) 100%);border:4px solid #fff;box-shadow:0 1px 4px rgba(0,0,0,.3)}
  .strip-bubble{position:absolute;left:10px;top:297px;width:110px;height:84px;border-radius:10px;background:var(--bubble);border:1px solid #c8c8c8;padding:10px 12px;color:var(--bubble-text)}
  .strip-bubble .date{font-size:13px;border-bottom:1px solid #ddd;padding-bottom:4px;white-space:nowrap}
  .strip-bubble .msg{font-size:17px;margin-top:8px;white-space:nowrap}
  .action-bar{position:absolute;left:0;top:1040px;width:105px;height:96px;background:var(--action-bar)}
  .add-button{position:absolute;left:25px;top:18px;width:90px;height:60px;border-radius:6px;background:var(--action-btn);color:#b5b5b5;font-size:34px;font-weight:300;line-height:58px;padding-left:22px}

  .menu-panel{position:absolute;left:0;top:0;width:535px;height:1136px;background:linear-gradient(180deg,var(--panel-top) 0%,var(--panel-mid) 28%,var(--panel-warm) 55%,var(--panel-low) 70%,var(--panel-bottom) 100%);color:var(--text-light)}

  .status-bar{position:absolute;left:0;top:0;width:640px;height:46px;color:var(--text-light);font-size:21px}
  .status-bar .carrier{position:absolute;left:12px;top:12px;display:flex;align-items:center;gap:6px}
  .dots{display:flex;gap:3px}
  .dots i{width:11px;height:11px;border-radius:50%;border:1.5px solid #fff;display:block}
  .dots i.on{background:#fff}
  .status-bar .time{position:absolute;left:0;width:640px;top:11px;text-align:center;font-weight:500}
  .status-bar .battery{position:absolute;right:10px;top:11px;display:flex;align-items:center;gap:8px}
  .status-bar .battery .bt{color:#7c8aa6}
  .battery-shape{width:46px;height:20px;border:2px solid #fff;border-radius:4px;padding:2px;position:relative}
  .battery-shape::before{content:"";display:block;width:100%;height:100%;background:#fff;border-radius:1px}
  .battery-shape::after{content:"";position:absolute;right:-6px;top:5px;width:3px;height:7px;background:#fff;border-radius:0 2px 2px 0}

  .settings-icon{position:absolute;left:46px;top:72px}
  .profile-photo{position:absolute;left:207px;top:116px;width:128px;height:128px;border-radius:50%;border:3px solid #fff;background:radial-gradient(circle at 50% 42%,#7a6350 0%,#3a4660 55%,#58684e 100%)}
  .welcome{position:absolute;left:0;top:264px;width:542px;text-align:center;font-size:22px;font-weight:700;color:var(--text-soft)}

  .menu-list{position:absolute;left:43px;top:298px;width:492px;list-style:none}
  .menu-item{position:relative;display:flex;align-items:center;font-size:33px;font-weight:300;border-bottom:1.5px solid var(--divider)}
  .menu-item .icon{position:absolute;left:8px;top:50%;transform:translateY(-50%)}
  .menu-item .label{position:absolute;left:72px;top:50%;transform:translateY(-52%);white-space:nowrap}
  .item-chats{height:98px}
  .item-about{height:101px}
  .item-help{height:92px}
  .item-terms{height:90px}
  .item-signout{height:96px;border-bottom:none}
  .badge{position:absolute;width:32px;height:32px;border-radius:50%;background:var(--badge);color:#fff;font-size:20px;font-weight:400;text-align:center;line-height:32px}
  .item-chats .badge{left:375px;top:29px}
  .chevron{position:absolute;left:452px;top:33px}

  .history-band{position:absolute;left:0;top:808px;width:535px;height:68px;background:var(--band)}
  .history-title{position:absolute;left:35px;top:16px;font-size:29px;font-weight:300}
  .history-count{position:absolute;left:166px;top:13px;width:42px;height:42px;border-radius:50%;background:var(--count);font-size:28px;font-weight:300;text-align:center;line-height:42px}
  .clear-button{position:absolute;left:380px;top:12px;width:114px;height:44px;border-radius:22px;background:var(--pill);font-size:29px;font-weight:300;text-align:center;line-height:43px}

  .history-list{position:absolute;left:43px;top:876px;width:492px;list-style:none}
  .history-item{position:relative;height:96px;border-bottom:1.5px solid rgba(255,255,255,.2)}
  .history-item:last-child{border-bottom:none}
  .history-item .icon{position:absolute;left:10px;top:24px}
  .history-item .when{position:absolute;left:72px;top:20px;font-size:33px;font-weight:300}
  .history-item .when small{font-size:21px}
  .history-item .words{position:absolute;left:72px;top:62px;font-size:20px;font-weight:300;color:var(--text-muted)}
  .history-item .badge{left:375px;top:26px}
</style>
</head>
<body>
<div class="screen">

  <section class="conversation-strip" role="img" aria-label="Blurred travel photo background behind the chat feed">
    <div class="strip-status"></div>
    <div class="strip-header"></div>
    <svg class="mail-icon" width="56" height="40" viewBox="0 0 56 40" aria-hidden="true">
      <rect x="2" y="8" width="44" height="30" fill="none" stroke="#333" stroke-width="2"/>
      <path d="M2 8 L24 26 L46 8" fill="none" stroke="#333" stroke-width="2"/>
      <circle cx="46" cy="8" r="8" fill="#fff" stroke="#333" stroke-width="1.5"/>
      <text x="46" y="12" font-family="Roboto,sans-serif" font-size="11" text-anchor="middle" fill="#333">2</text>
    </svg>
    <div class="strip-avatar" style="top:145px" role="img" aria-label="Chat member profile photo"></div>
    <div class="strip-bubble">
      <div class="date">19/04/2015. 5</div>
      <div class="msg">Lorem Ips</div>
    </div>
    <div class="strip-avatar" style="top:445px" role="img" aria-label="Chat member profile photo"></div>
    <div class="strip-avatar" style="top:695px" role="img" aria-label="Chat member profile photo"></div>
    <div class="action-bar"><div class="add-button">+</div></div>
  </section>

  <nav class="menu-panel">
    <svg class="settings-icon" width="44" height="44" viewBox="0 0 44 44" aria-hidden="true">
      <g fill="none" stroke="#fff" stroke-width="2">
        <path d="M19 3h6l1 5 4 2 4-3 4 4-3 4 2 4 5 1v6l-5 1-2 4 3 4-4 4-4-3-4 2-1 5h-6l-1-5-4-2-4 3-4-4 3-4-2-4-5-1v-6l5-1 2-4-3-4 4-4 4 3 4-2z"/>
        <circle cx="22" cy="22" r="8"/>
      </g>
    </svg>
    <div class="profile-photo" role="img" aria-label="User profile photo"></div>
    <p class="welcome">Welcome Marlow Hayes!</p>

    <ul class="menu-list">
      <li class="menu-item item-chats">
        <svg class="icon" width="50" height="44" viewBox="0 0 50 44" aria-hidden="true"><g fill="none" stroke="#fff" stroke-width="1.8"><path d="M16 3c-8 0-14 5-14 11 0 4 2 7 6 9l-2 6 7-4c1 0 2 .2 3 .2"/><path d="M16 3c8 0 14 5 14 11"/><path d="M32 15c-9 0-15 5-15 11s6 11 15 11c1.5 0 2.5 0 3.5-.3l6 4-1.5-6c4-2 6.5-5 6.5-8.7 0-6-6-11-14.5-11z"/></g></svg>
        <span class="label">Chats</span>
        <span class="badge">2</span>
        <svg class="chevron" width="22" height="34" viewBox="0 0 22 34" aria-hidden="true"><path d="M3 2l16 15L3 32" fill="none" stroke="#9aa2b2" stroke-width="3"/></svg>
      </li>
      <li class="menu-item item-about">
        <svg class="icon" width="52" height="52" viewBox="0 0 52 52" aria-hidden="true"><circle cx="26" cy="26" r="24" fill="none" stroke="#fff" stroke-width="1.8"/><path d="M26 14v26" stroke="#fff" stroke-width="1.8"/></svg>
        <span class="label">About Kite Chat</span>
      </li>
      <li class="menu-item item-help">
        <svg class="icon" width="52" height="52" viewBox="0 0 52 52" aria-hidden="true"><circle cx="26" cy="26" r="24" fill="none" stroke="#fff" stroke-width="1.8"/><text x="26" y="36" font-family="Roboto,sans-serif" font-weight="300" font-size="28" text-anchor="middle" fill="#fff">?</text></svg>
        <span class="label">Help</span>
      </li>
      <li class="menu-item item-terms">
        <svg class="icon" width="52" height="40" viewBox="0 0 52 40" aria-hidden="true"><g fill="none" stroke="#fff" stroke-width="1.6"><rect x="8" y="2" width="42" height="34"/><path d="M8 8H2v28h6"/><rect x="14" y="18" width="12" height="10"/><path d="M14 10h30M30 18h14M30 23h14M30 28h14"/></g></svg>
        <span class="label">Terms &amp; Condition</span>
      </li>
      <li class="menu-item item-signout">
        <svg class="icon" width="54" height="54" viewBox="0 0 54 54" aria-hidden="true"><g fill="none" stroke="#fff" stroke-width="2.5"><path d="M17 10A22 22 0 1 0 37 10"/><path d="M27 2v24"/></g></svg>
        <span class="label">Sign Out</span>
      </li>
    </ul>

    <div class="history-band">
      <span class="history-title">Histry</span>
      <span class="history-count">2</span>
      <span class="clear-button">Clear</span>
    </div>

    <ul class="history-list">
      <li class="history-item">
        <svg class="icon" width="48" height="42" viewBox="0 0 50 44" aria-hidden="true"><g fill="none" stroke="#fff" stroke-width="1.8"><path d="M16 3c-8 0-14 5-14 11 0 4 2 7 6 9l-2 6 7-4c1 0 2 .2 3 .2"/><path d="M16 3c8 0 14 5 14 11"/><path d="M32 15c-9 0-15 5-15 11s6 11 15 11c1.5 0 2.5 0 3.5-.3l6 4-1.5-6c4-2 6.5-5 6.5-8.7 0-6-6-11-14.5-11z"/></g></svg>
        <span class="when">5 mIn</span>
        <span class="words">Apple, Like, Ship, Wonder.</span>
        <span class="badge">3</span>
      </li>
      <li class="history-item">
        <svg class="icon" width="48" height="42" viewBox="0 0 50 44" aria-hidden="true"><g fill="none" stroke="#fff" stroke-width="1.8"><path d="M16 3c-8 0-14 5-14 11 0 4 2 7 6 9l-2 6 7-4c1 0 2 .2 3 .2"/><path d="M16 3c8 0 14 5 14 11"/><path d="M32 15c-9 0-15 5-15 11s6 11 15 11c1.5 0 2.5 0 3.5-.3l6 4-1.5-6c4-2 6.5-5 6.5-8.7 0-6-6-11-14.5-11z"/></g></svg>
        <span class="when">7:09 <small>Am</small></span>
        <span class="words">Apple, Like, Ship, Wonder.</span>
      </li>
    </ul>
  </nav>

  <header class="status-bar">
    <div class="carrier"><span class="dots"><i class="on"></i><i class="on"></i><i class="on"></i><i></i><i></i></span><span>NOVA</span>
      <svg width="22" height="16" viewBox="0 0 22 16" aria-hidden="true"><g fill="none" stroke="#fff" stroke-width="2.2"><path d="M2 6a13 13 0 0 1 18 0"/><path d="M5.5 9.5a8 8 0 0 1 11 0"/></g><circle cx="11" cy="13.5" r="2" fill="#fff"/></svg>
    </div>
    <div class="time">4:21 PM</div>
    <div class="battery"><span class="bt">✱</span><span>100%</span><span class="battery-shape"></span></div>
  </header>

</div>
</body>
</html>
```